Biz Card

MARKETING today is the most rapidly changing business discipline. Media options to reach customers, actual customer preferences and consumer buying decisions change by the minute . . . no, by the second. The behavioral data generated by all aspects of the business and the new technologies that put the data to work together produce the potential to generate business intelligence and guide smart resource allocation to influence purchase and retention. However, to realize this potential, marketing professionals at all levels and in all organizations must continuously improve their skills not just from on-the-job training but by learning from masters in the field. The Bright Horizon Guild is the training center that serves this professional development need.model logos:msi.orgama.orgcontentmarketinginstitute.comBook covers on MarketingMetrics, Marketing Anaytics
Industry/Entity Type
Business
Contact Information for Business Card
Roy A. YoungCEOMarketing Science Academyphone: 310-601-4755email: roy@marketingscience.comAddress:437 South Rexford DriveBeverly Hills, CA 89377
Look and feel
Each slider illustrates characteristics of the customer's brand and the style your logo design should communicate.

```html
<!DOCTYPE html>
<html lang="en">
<head>
<meta charset="utf-8">
<title>Bright Horizon Guild – Business Card</title>
<link rel="stylesheet" href="https://fonts.googleapis.com/css2?family=Montserrat:wght@400&family=Roboto:wght@400;500&family=Roboto+Condensed:wght@700&display=swap">
<style>
  :root {
    --backdrop: #b1afb0;
    --brand-orange: #e27b22;
    --card-white: #fbfbfb;
    --ring-grey: #9c9c9c;
    --text-dark: #3f3f3f;
    --text-white: #ffffff;
  }
  html, body {
    margin: 0;
    padding: 0;
    width: 1200px;
    height: 1200px;
    overflow: hidden;
    background: var(--backdrop);
  }
  .canvas {
    position: relative;
    width: 1200px;
    height: 1200px;
  }
  .card {
    position: absolute;
    box-sizing: border-box;
  }
  .card-front {
    left: 238px;
    top: 117px;
    width: 714px;
    height: 420px;
    background: var(--brand-orange);
  }
  .card-back {
    left: 230px;
    top: 645px;
    width: 713px;
    height: 416px;
    background: var(--card-white);
  }
  .front-ring {
    position: absolute;
    left: 157px;
    top: 136px;
    width: 150px;
    height: 150px;
  }
  .front-name {
    position: absolute;
    left: 337px;
    top: 145px;
    margin: 0;
    font-family: "Montserrat", sans-serif;
    font-weight: 400;
    font-size: 38px;
    line-height: 42px;
    letter-spacing: 0.5px;
    color: var(--text-white);
  }
  .back-ring {
    position: absolute;
    left: 70px;
    top: 174px;
    width: 64px;
    height: 64px;
  }
  .back-name {
    position: absolute;
    left: 150px;
    top: 155px;
    margin: 0;
    font-family: "Montserrat", sans-serif;
    font-weight: 400;
    font-size: 28px;
    line-height: 34px;
    color: var(--brand-orange);
  }
  .contact {
    position: absolute;
    left: 377px;
    top: 100px;
    font-family: "Roboto", sans-serif;
    color: var(--text-dark);
  }
  .person-name {
    margin: 0;
    font-family: "Roboto Condensed", sans-serif;
    font-weight: 700;
    font-size: 25px;
    line-height: 32px;
    color: var(--brand-orange);
  }
  .person-title {
    margin: 4px 0 0;
    font-size: 15px;
    line-height: 18px;
  }
  .address {
    margin: 30px 0 0;
    font-style: normal;
    font-size: 17.5px;
    line-height: 24px;
  }
  .contact-list {
    list-style: none;
    margin: 5px 0 0;
    padding: 0;
    font-size: 17.5px;
    line-height: 24px;
  }
  .contact-list li {
    display: flex;
    align-items: center;
  }
  .contact-icon {
    width: 16px;
    height: 16px;
    margin: 0 19px 0 1px;
    flex: none;
  }
</style>
</head>
<body>
<main class="canvas">
  <section class="card card-front">
    <svg class="front-ring" viewBox="0 0 150 150" aria-hidden="true">
      <circle cx="75" cy="75" r="71" fill="none" stroke="var(--text-white)" stroke-width="6"/>
    </svg>
    <h1 class="front-name">Bright<br>Horizon<br>Guild</h1>
  </section>

  <section class="card card-back">
    <svg class="back-ring" viewBox="0 0 64 64" aria-hidden="true">
      <circle cx="32" cy="32" r="28" fill="none" stroke="var(--ring-grey)" stroke-width="6"/>
    </svg>
    <p class="back-name">Bright<br>Horizon<br>Guild</p>

    <div class="contact">
      <h2 class="person-name">Neil P. Barton</h2>
      <p class="person-title">CEO</p>
      <address class="address">912 North Calloway Lane<br>Beverly Hills, CA 89377</address>
      <ul class="contact-list">
        <li>
          <svg class="contact-icon" viewBox="0 0 16 16" aria-hidden="true">
            <path d="M1 6 Q8 1 15 6 L13 8 L10.5 6.5 L10.5 5 Q8 4.2 5.5 5 L5.5 6.5 L3 8 Z" fill="var(--brand-orange)"/>
            <rect x="3" y="9" width="10" height="5" rx="1" fill="var(--brand-orange)"/>
          </svg>
          310-555-0182
        </li>
        <li>
          <svg class="contact-icon" viewBox="0 0 16 16" aria-hidden="true">
            <rect x="1" y="3" width="14" height="10" fill="var(--brand-orange)"/>
            <path d="M1 3 L8 9 L15 3" fill="none" stroke="var(--card-white)" stroke-width="1.3"/>
          </svg>
          neil@brighthorizonguild.com
        </li>
        <li>
          <svg class="contact-icon" viewBox="0 0 16 16" aria-hidden="true">
            <circle cx="8" cy="8" r="7" fill="var(--brand-orange)"/>
            <path d="M1 8 H15 M8 1 V15 M3 4.5 H13 M3 11.5 H13" stroke="var(--card-white)" stroke-width="0.9" fill="none"/>
            <ellipse cx="8" cy="8" rx="3" ry="7" fill="none" stroke="var(--card-white)" stroke-width="0.9"/>
          </svg>
          www.brighthorizonguild.com
        </li>
      </ul>
    </div>
  </section>
</main>
</body>
</html>
```